Strategy and Technology Consulting - Our Story and Values Page

Interior Page design – Our History and Our Values

Our homepage has been designed and we are looking for a design for one of the interior pages. This interior page tells the story of Our History and Our Values

Because the homepage has been designed, we would like this interior page to reflect the design of the homepage without being a mirror image of the homepage.

This site will be implemented in WordPress using the Elementor framework.

Font: Poppins medium and Poppins dark
Illustrations: Our homepage illustrations were designed by “Brelin 1974” on Quillmark. Compatible original or stock illustrations are welcome. Stock photography is also welcome. Brelin is also available through Brelin Tosamek on Ravolo

Uploaded Files
• Homepage design – this is the design we will use for our homepage. Contest entries should reflect this basic style but should be distinctly different from the homepage.
• Our History and Our Values – Wireframe – the basic layout of the page we are looking for.
• Our History and Our Values – Word document with the text supporting the wireframe.
• Color Palette – please use colors compatible with the palette attached.

Our Story - timeline
There is a timeline element in the wireframe. The wireframe displays this as a series of chevrons (arrows), but it does not need to be. Creativity in display of the timeline is appreciated.

Our Values
If you look at the Word document, you will see that there are a lot of words on the page. The winning design will present the information in a way that engages the user without overwhelming them with too much to read. For example, they may click on a value and see more information.

Target Market(s)

CIO's and Technology Executives

Number of Pages Required

1 page

Font styles to use
Sans Serif
Other font styles liked:
• Poppin

Requirements
Must have
• A timeline element, all of our values
Nice to have
• Clever timeline display

```html
<!DOCTYPE html>
<html lang="en">
<head>
<meta charset="utf-8">
<title>Veridane – Our Story and Values</title>
<link href="https://fonts.googleapis.com/css2?family=Poppins:wght@400;500;600;700;800&display=swap" rel="stylesheet">
<style>
:root{
  --blue:#2f6aa3;
  --yellow:#e9b91a;
  --yellow-soft:#f1b92a;
  --grey:#dcdcdc;
  --ink:#111111;
  --text:#333333;
  --navy:#44536a;
  --navy-dark:#3a4658;
  --white:#ffffff;
}
*{box-sizing:border-box;margin:0;padding:0}
html,body{width:1200px;height:2614px;overflow:hidden}
body{position:relative;font-family:"Poppins",sans-serif;color:var(--text);background:var(--white)}
.abs{position:absolute}

/* header */
.site-header{left:0;top:0;width:1200px;height:90px;background:var(--white);box-shadow:0 2px 8px rgba(0,0,0,.05);z-index:2}
.brand{left:92px;top:18px;display:flex;align-items:center;gap:10px;font-size:46px;font-weight:400;color:#8a8f96;letter-spacing:1px}
.brand-dot{width:14px;height:14px;background:var(--blue)}
.main-nav{left:544px;top:36px;display:flex;gap:22px;align-items:center;font-size:13px;font-weight:600;color:#3c4a60}
.home-icon{width:16px;height:14px}
.nav-item::after{content:" ⌄";font-size:11px}
.btn-contact{background:var(--yellow);color:var(--white);font-weight:700;font-size:12px;border-radius:22px;display:flex;align-items:center;justify-content:center}
.header-cta{left:981px;top:26px;width:132px;height:40px}

/* story */
.story{left:0;top:90px;width:1200px;height:617px;background:linear-gradient(135deg,#f4f4f6,#e9e9ec 60%,#f2f2f4)}
.story-title{left:0;top:166px;width:1230px;text-align:center;font-size:37px;font-weight:700;color:var(--ink)}
.timeline-line{left:360px;top:299px;width:500px;height:1px;background:#999}
.chevron{top:272px;width:252px;height:56px;display:flex;align-items:center;justify-content:center;font-size:19px;font-weight:700;clip-path:polygon(0 0,88% 0,100% 50%,88% 100%,0 100%,8% 50%)}
.chev-1{left:120px;background:var(--blue);color:var(--white)}
.chev-2{left:474px;background:var(--yellow);color:var(--ink)}
.chev-3{left:828px;background:var(--grey);color:#444;font-weight:600}
.dash{top:328px;width:0;height:72px;border-left:1px dashed}
.dash-1{left:225px;border-color:var(--blue)}
.dash-2{left:601px;border-color:var(--yellow)}
.dash-3{left:955px;border-color:#bbb}
.story-card{top:400px;width:314px;height:208px;background:var(--white);border-radius:6px;padding:30px 14px 30px 24px;font-size:14.8px;line-height:27px;color:#333}
.story-card.c1{left:89px;border:2px solid var(--blue)}
.story-card.c2{left:444px;border:2px solid var(--yellow)}
.story-card.c3{left:798px;border:2px solid #ddd}
.story-card p::before{content:"";display:inline-block;width:12px;height:12px;border-radius:50%;background:#222;margin-right:4px;vertical-align:-1px}
.story-card p.sub::before{content:"-";width:auto;height:auto;background:none;margin:0 12px 0 0}

/* values */
.values-title{left:104px;top:764px;font-size:36px;font-weight:700;color:var(--ink)}
.deco{background:linear-gradient(135deg,rgba(47,106,163,.0),rgba(47,106,163,.55) 45%,rgba(150,160,240,.6));opacity:.9}
.deco-top{left:1030px;top:732px;width:170px;height:112px;clip-path:polygon(100% 0,100% 60%,0 100%,30% 40%)}
.deco-bottom{left:0;top:1680px;width:236px;height:150px;clip-path:polygon(100% 0,80% 60%,20% 100%,0 100%,0 70%)}
.value-card{width:459px;background:var(--white);border-radius:4px;box-shadow:0 2px 14px rgba(0,0,0,.09);padding:18px 12px 0 114px}
.value-icon{left:16px;top:16px;width:80px;height:80px;border-radius:50%;background:var(--yellow);display:flex;align-items:center;justify-content:center}
.value-icon svg{width:48px;height:48px;fill:none;stroke:#1a1a1a;stroke-width:2;stroke-linejoin:round;stroke-linecap:round}
.value-card h3{font-size:21px;font-weight:600;color:var(--ink);line-height:30px;margin-bottom:6px;margin-top:2px}
.value-card p{font-size:12.6px;line-height:21.6px;color:#222}
.value-card.sm p{font-size:12px}

/* newsletter */
.newsletter-band{left:0;top:1890px;width:1200px;height:670px;background:linear-gradient(180deg,var(--navy) 0%,#4d5d76 60%,#5a6b84 100%)}
.wave{left:0;top:1880px;width:1200px;height:320px}
.subscribe{left:126px;top:1888px;width:947px;height:212px;border-radius:106px;background:var(--yellow-soft)}
.subscribe h2{left:82px;top:56px;font-size:33px;font-weight:800;color:var(--white)}
.subscribe p{left:83px;top:110px;width:440px;font-size:16px;line-height:20px;font-weight:500;color:var(--white)}
.email-field{left:562px;top:82px;width:328px;height:48px;border-radius:24px;background:var(--white);display:flex;align-items:center;padding-left:24px;font-size:13px;color:#888;gap:10px}
.send{position:absolute;right:6px;top:6px;width:38px;height:38px;border-radius:50%;background:#9fb2c4;display:flex;align-items:center;justify-content:center}

/* footer */
.footer-brand{left:110px;top:2280px;font-size:64px;color:#c9ced6;font-weight:400;display:flex;align-items:center;gap:10px}
.footer-brand .brand-dot{width:16px;height:16px;background:var(--yellow)}
.social{top:2365px;width:42px;height:42px;border-radius:50%;background:rgba(255,255,255,.18)}
.footer-cta{left:205px;top:2429px;width:135px;height:40px}
.footer-col h4{font-size:20px;font-weight:800;color:var(--white);margin-bottom:18px}
.footer-col li{list-style:none;font-size:13px;color:#e6e9ee;line-height:32px}
.footer-col li::before{content:"› ";font-size:15px}
.contact-item{display:flex;gap:10px;font-size:13px;color:#e6e9ee;line-height:18px;margin-bottom:20px}
.contact-ico{width:14px;height:14px;margin-top:2px;flex:none}
.copyright{left:0;top:2555px;width:1200px;height:59px;background:var(--navy-dark);color:var(--white);font-size:14px;font-weight:500;display:flex;align-items:center;justify-content:center}
.chat-bubble{left:1147px;top:2530px;width:50px;height:50px;border-radius:50%;background:var(--yellow)}
</style>
</head>
<body>

<header class="abs site-header">
  <div class="abs brand"><span class="brand-dot"></span>Veridane</div>
  <nav class="abs main-nav">
    <svg class="home-icon" viewBox="0 0 16 14"><path d="M8 0 0 7h2v7h4V9h4v5h4V7h2z" fill="#7f93a8"/></svg>
    <span class="nav-item">ABOUT US</span>
    <span class="nav-item">SERVICES</span>
    <span class="nav-item">INSIGHTS</span>
    <span class="nav-item">JOIN US</span>
  </nav>
  <a class="abs btn-contact header-cta">CONTACT US</a>
</header>

<section class="abs story"></section>
<h1 class="abs story-title">Our Story</h1>
<div class="abs timeline-line"></div>
<div class="abs chevron chev-1">2018 – 2019</div>
<div class="abs chevron chev-2">2020 – 2021</div>
<div class="abs chevron chev-3">2022 and Onward</div>
<div class="abs dash dash-1"></div>
<div class="abs dash dash-2"></div>
<div class="abs dash dash-3"></div>
<div class="abs story-card c1">
  <p>Growth Strategy Focus</p>
  <p>Consistent, Modest Growth</p>
  <p>Preliminary Focus on Technology</p>
  <p>Eureka! &nbsp;- Implementing strategy is hard.</p>
</div>
<div class="abs story-card c2">
  <p>Pandemic Pauses Growth</p>
  <p>Rethinking :</p>
  <p class="sub">the business model</p>
  <p class="sub">the delivery model</p>
</div>
<div class="abs story-card c3">
  <p>Leadership Team for Focus on Essential Areas</p>
  <p>Rapid Growth</p>
  <p>Customer Success</p>
</div>

<h2 class="abs values-title">Our Values</h2>
<div class="abs deco deco-top" role="img" aria-label="Scattered blue and yellow squares decoration"></div>
<div class="abs deco deco-bottom" role="img" aria-label="Scattered blue and yellow squares decoration"></div>

<article class="abs value-card" style="left:124px;top:851px;height:241px">
  <div class="abs value-icon" aria-hidden="true"><svg viewBox="0 0 48 48"><path d="M18 8h14l5 6-12 12-12-12z"/><path d="M13 14h24M25 26l-4-12M25 26l4-12"/><path d="M4 38h6v-8H4zM10 32h8l6 2h6a2 2 0 0 1 0 4h-8M30 38l10-6a2 2 0 0 1 3 3l-11 7H10"/></svg></div>
  <h3>The Value of Every Human. Regardless.</h3>
  <p>Each person's unique experiences and perspectives add vibrant hues to the tapestry of our shared existence. &nbsp;In a world where diversity paints the canvas of humanity, true beauty is found in recognizing the inherent and incalculable value of every human being.</p>
</article>
<article class="abs value-card sm" style="left:618px;top:851px;height:241px">
  <div class="abs value-icon" aria-hidden="true"><svg viewBox="0 0 48 48"><path d="M8 30l10-12 6 4 6-4 10 12-10 10-6-4-6 4z"/><path d="M18 26l6 6M22 24l6 6M24 6v5M14 9l3 4M34 9l-3 4"/></svg></div>
  <h3>Collaboration</h3>
  <p>Collaboration in work transforms individual endeavors into symphonies of collective achievement. Through collaboration, diverse talents converge, fostering a rich exchange of ideas that amplifies creativity, accelerates progress, and brings forth solutions beyond what a single mind could conceive.</p>
</article>
<article class="abs value-card" style="left:124px;top:1121px;height:209px">
  <div class="abs value-icon" aria-hidden="true"><svg viewBox="0 0 48 48"><rect x="5" y="14" width="38" height="26" rx="3"/><path d="M17 14V9h14v5M5 24h38M21 24v4h6v-4"/></svg></div>
  <h3>Passion</h3>
  <p>Passion infuses our work with energy, transforming routine tasks into opportunities for creativity and innovation. Fueled by passion, individuals become unstoppable forces, driven to overcome challenges and achieve remarkable outcomes that benefit them and inspire those around them</p>
</article>
<article class="abs value-card" style="left:618px;top:1121px;height:209px">
  <div class="abs value-icon" aria-hidden="true"><svg viewBox="0 0 48 48"><circle cx="24" cy="18" r="12"/><circle cx="24" cy="18" r="7"/><path d="M17 28l-5 14 6-3 3 5 3-10M31 28l5 14-6-3-3 5-3-10"/></svg></div>
  <h3>Excellence</h3>
  <p>Excellence isn't a destination; it's a continuous journey of refinement and growth. Striving for excellence cultivates a culture of continuous improvement, fostering innovation, credibility, and a lasting impact that resonates far beyond the immediate task.</p>
</article>
<article class="abs value-card" style="left:124px;top:1359px;height:206px">
  <div class="abs value-icon" aria-hidden="true"><svg viewBox="0 0 48 48"><path d="M4 40l14-18 6 8 8-12 12 22z"/><path d="M32 18V6l8 3-8 3"/></svg></div>
  <h3>Tenacity</h3>
  <p>Tenacity is the unwavering anchor that keeps us grounded amidst adversity, propelling us forward when faced with obstacles. The resilience to persist, adapt, and learn from setbacks leads to the mastery of skills and the fulfillment of ambitious goals.</p>
</article>
<article class="abs value-card sm" style="left:618px;top:1359px;height:206px">
  <div class="abs value-icon" aria-hidden="true"><svg viewBox="0 0 48 48"><path d="M14 12h8a3 3 0 0 1 6 0h6v8a3 3 0 0 1 0 6v8H28a3 3 0 0 0-6 0h-8v-8a3 3 0 0 0 0-6z"/><path d="M24 34v10M8 8l3 3M40 8l-3 3M6 24h3M42 24h-3"/></svg></div>
  <h3>Solution Mindset</h3>
  <p>A solution mindset is the compass that directs our focus from problems to possibilities. It empowers us to navigate challenges with a proactive mindset, igniting a journey of exploration and innovation that not only resolves issues but also paves the way for continuous growth and success.</p>
</article>
<article class="abs value-card" style="left:371px;top:1594px;height:213px">
  <div class="abs value-icon" aria-hidden="true"><svg viewBox="0 0 48 48"><rect x="8" y="6" width="12" height="12"/><rect x="28" y="6" width="12" height="12"/><path d="M8 12h12M28 12h12"/><path d="M24 42L12 31a7 7 0 0 1 12-7 7 7 0 0 1 12 7z"/></svg></div>
  <h3>Generosity</h3>
  <p>Generosity creates a virtuous cycle of goodwill, fostering a sense of unity and shared purpose among colleagues. By freely sharing knowledge, support, and resources, we uplift those around us and contribute to a collaborative environment where collective achievements flourish.</p>
</article>

<div class="abs newsletter-band"></div>
<svg class="abs wave" viewBox="0 0 1200 320" preserveAspectRatio="none">
  <path d="M0 0H1200V120C1100 130 1020 220 900 270C760 330 560 290 420 230C280 170 120 30 0 20Z" fill="#d9dce1"/>
  <path d="M0 0H1200V110C1100 120 1020 205 900 255C760 312 560 275 420 215C280 158 120 20 0 10Z" fill="#ffffff"/>
</svg>
<section class="abs subscribe">
  <h2 class="abs">Subscribe Our Newsletter</h2>
  <p class="abs">Subscribe our newsletter to receive the latest news and exclusive offers every week, No spam.</p>
  <div class="abs email-field">
    <svg width="14" height="11" viewBox="0 0 14 11"><rect width="14" height="11" rx="1" fill="#9aa5b3"/><path d="M0 1l7 5 7-5" stroke="#fff" fill="none"/></svg>
    Enter email address
    <span class="send"><svg width="14" height="14" viewBox="0 0 14 14"><path d="M0 6 14 0 9 14 7 8z" fill="#fff"/></svg></span>
  </div>
</section>

<div class="abs footer-brand"><span class="brand-dot"></span>Veridane</div>
<span class="abs social" style="left:166px"></span>
<span class="abs social" style="left:218px"></span>
<span class="abs social" style="left:270px"></span>
<span class="abs social" style="left:321px"></span>
<a class="abs btn-contact footer-cta">CONTACT US</a>

<div class="abs footer-col" style="left:488px;top:2258px">
  <h4>Quick links</h4>
  <ul><li>Home</li><li>About Us</li><li>Services</li><li>Insights</li><li>Join Us</li><li>Contact Us</li></ul>
</div>
<div class="abs footer-col" style="left:669px;top:2258px">
  <h4>Our Services</h4>
  <ul><li>Business Transformation</li><li>ERP Implementations</li><li>ERP Solutions</li><li>BI and Data</li><li>Building the Right Team...</li></ul>
</div>
<div class="abs footer-col" style="left:906px;top:2258px">
  <h4>Contact info</h4>
  <div class="contact-item"><svg class="contact-ico" viewBox="0 0 14 14"><rect y="2" width="14" height="10" fill="#e9b91a"/></svg><span>Email:<br>hello@veridane-mail.com</span></div>
  <div class="contact-item"><svg class="contact-ico" viewBox="0 0 14 14"><path d="M3 0l3 3-2 2c1 2 3 4 5 5l2-2 3 3-2 3C6 14 0 8 0 3z" fill="#e9b91a"/></svg><span>Phone:<br>+44 113 555 0192</span></div>
  <div class="contact-item"><svg class="contact-ico" viewBox="0 0 14 14"><path d="M7 0a5 5 0 0 1 5 5c0 4-5 9-5 9S2 9 2 5a5 5 0 0 1 5-5z" fill="#e9b91a"/><circle cx="7" cy="5" r="2" fill="#4d5d76"/></svg><span>Location:<br>Some address line goes<br>here city name</span></div>
</div>

<footer class="abs copyright">© Veridane Design 2023, All Rights Reserved</footer>
<div class="abs chat-bubble"></div>

</body>
</html>
```